Website Redesign Project Puzzle Vault Larkfield

We are an escape room company located in Ashburn, Virginia. We currently have a website https://www.puzzlevaultlarkfield.example based upon html/bootstrap/javascript/php/mysql and I'd like to keep it that way. I'm looking for someone upgrade the front page so it is more informative, cleaner, quicker to load, and optimizes the space for full sale opportunities.

Target Market(s)

Corporate Clients, Families, Friends. All ages

Industry/Entity Type

Entertainment Industry

Coding

Coded - Design and coding required

Number of Pages Required

3 page

Font styles to use
Other font styles liked:
• Similar to Facebook or Amazon

Requirements
Must have
• Must be mobile friendly. bootstrap. Lots of graphics (will provide) nice and easy to read fonts. Easy to read layout. Must look clean, fresh, exciting, and want to grab attention.
• Please visit my facebook page and website for more details. facebook.com/puzzlevaultlarkfield
Nice to have
• Same color as existing but open to options if they look nice.
Should not have
• Should not be wordpress or hard to modify.

```html
<!DOCTYPE html>
<html lang="en">
<head>
<meta charset="utf-8">
<title>Puzzle Vault Larkfield</title>
<link href="https://fonts.googleapis.com/css2?family=Titillium+Web:wght@400;600;700&display=swap" rel="stylesheet">
<style>
:root{
  --blue:#1c8fdc;
  --blue-bright:#2a9de2;
  --blue-frame:#4cbcf0;
  --ink:#1b1b1b;
  --text:#333;
  --muted:#555;
  --grey-bg:#f2f3f5;
  --line:#d8dbe0;
  --black:#050505;
  --white:#fff;
}
*{box-sizing:border-box;margin:0;padding:0}
html,body{width:1200px;height:5093px;overflow:hidden}
body{font-family:"Titillium Web",Arial,sans-serif;color:var(--text);background:var(--white);position:relative}
.abs{position:absolute}
.center{text-align:center}
.btn{position:absolute;display:flex;align-items:center;justify-content:center;background:var(--blue-bright);color:var(--white);border-radius:22px;font-size:12px;font-weight:600;text-transform:uppercase;letter-spacing:.3px}

/* header */
.site-header{left:0;top:0;width:1200px;height:136px;background:var(--black)}
.brand{left:113px;top:38px;display:flex;align-items:center;gap:12px;color:var(--blue-bright);font-weight:700;font-size:26px;line-height:1}
.brand-mark{width:40px;height:40px;border:3px solid var(--blue-bright)}
.nav{left:398px;top:50px;display:flex;gap:36px;color:var(--white);font-size:13px;font-weight:600;text-transform:uppercase}
.nav .active{position:relative}
.nav .active::after{content:"";position:absolute;left:0;right:0;top:26px;height:2px;background:var(--blue-bright)}

/* hero */
.hero{left:0;top:136px;width:1200px;height:643px;background:linear-gradient(180deg,#3a1420 0%,#8a1a2e 45%,#b81e38 60%,#2b1220 100%)}
.dots{left:570px;top:700px;display:flex;gap:10px}
.dots span{width:12px;height:12px;border-radius:50%;background:var(--white)}
.dots span.on{background:var(--blue-bright)}

/* rooms */
.room-card{top:856px;width:231px;height:391px;border:2px solid var(--blue-frame);background:var(--white)}
.room-photo{height:156px}
.room-card h3{margin-top:18px;color:var(--blue-bright);font-size:17px;font-weight:700;text-transform:uppercase;letter-spacing:.5px;text-align:center}
.room-card .diff{font-size:12px;text-align:center;margin-top:2px}
.room-card p{font-size:12px;line-height:20px;text-align:center;padding:8px 26px 0}
.room-card .btn{left:53px;top:326px;width:122px;height:38px}

/* corporate */
.corporate{left:0;top:1328px;width:1200px;height:1545px;background:var(--grey-bg)}
h2.section-title{position:absolute;left:0;width:1200px;text-align:center;font-size:32px;font-weight:700;color:var(--ink);text-transform:uppercase}
.corp-frame{left:111px;top:1473px;width:976px;height:472px;background:var(--blue-frame);padding:12px}
.corp-photo{width:100%;height:100%;background:linear-gradient(135deg,#27467a,#4d74a8 50%,#c8a48c)}
.packages-title{left:0;width:1200px;top:1998px;color:var(--blue-bright);font-size:33px;font-weight:700;text-transform:uppercase}
.pkg-circle{top:2091px;width:206px;height:206px;border-radius:50%;background:var(--blue);border:5px solid var(--white);box-shadow:0 0 0 2px #cfe6f7;display:flex;align-items:center;justify-content:center}
.pkg-name{top:2318px;width:330px;font-size:14px;font-weight:700;color:var(--ink);text-transform:uppercase}
.pkg-desc{top:2355px;width:330px;font-size:13px;line-height:20px}
.field{position:absolute;background:var(--white);border:1px solid var(--line);font-size:13px;color:#444;padding:10px 22px}

/* birthday */
.intro{left:170px;top:2998px;width:860px;font-size:13px;line-height:28px}
.price-card{top:3112px;width:433px;height:482px;border:1px solid #e4e4e4;background:var(--white)}
.price-head{height:114px;background:#efefef;text-align:center;padding-top:30px;font-size:25px;font-weight:600;color:var(--ink)}
.price-badge{position:absolute;left:152px;top:79px;width:130px;height:130px;border-radius:50%;background:var(--blue);border:5px solid var(--white);box-shadow:0 0 0 1px #ddd;color:var(--white);font-size:27px;font-weight:600;line-height:28px;display:flex;flex-direction:column;align-items:center;justify-content:center}
.price-list{position:absolute;left:48px;top:270px;list-style:none;font-size:13px}
.price-list li{display:flex;align-items:center;gap:12px;height:42px}
.price-rule{position:absolute;left:0;right:0;top:375px;border-top:1px solid #eee}
.ghost{position:absolute;top:418px;left:92px;width:117px;height:36px;border:1px solid #999;border-radius:20px;font-size:13px;color:#777;display:flex;align-items:center;justify-content:center}
.solid{position:absolute;top:418px;left:225px;width:117px;height:36px;background:#111;color:var(--white);border-radius:20px;font-size:13px;font-weight:600;display:flex;align-items:center;justify-content:center}
.note{left:0;width:1200px;top:3636px;color:var(--blue-bright);font-size:19px}

/* blue form */
.contact-band{left:0;top:3730px;width:1200px;height:390px;background:linear-gradient(180deg,#1e95dc,#1b8ad6)}
.band-btn{left:512px;top:4001px;width:176px;height:52px;border:2px solid var(--white);border-radius:26px;color:var(--white);font-size:13px;font-weight:600;display:flex;align-items:center;justify-content:center;text-transform:uppercase}

/* faq */
.faq-intro{left:150px;top:4190px;width:900px;font-size:23px;line-height:36px;color:#444}
.faq-item{position:absolute;width:468px;height:54px;border:1px solid var(--line);display:flex;align-items:center;gap:14px;padding-left:12px;font-size:14px}

/* footer */
.site-footer{left:0;top:4626px;width:1200px;height:467px;background:var(--black);color:var(--white)}
.ct-circle{top:4785px;width:94px;height:94px;border-radius:50%;background:var(--blue);border:4px solid var(--white);display:flex;align-items:center;justify-content:center}
.ct-text{top:4896px;width:260px;font-size:14px;line-height:21px;text-align:center}
.footer-rule{left:111px;top:5012px;width:978px;border-top:1px solid #333}
.copyright{left:0;width:1200px;top:5038px;font-size:13px;text-align:center}
</style>
</head>
<body>

<header class="abs site-header">
  <div class="abs brand"><span class="brand-mark"></span><span>PUZZLE VAULT<br>LARKFIELD</span></div>
  <nav class="abs nav">
    <span class="active">Home</span><span>Escape Rooms</span><span>Corporate Events</span><span>Birthday Parties</span><span>FAQs</span><span>Contact Us</span>
  </nav>
</header>

<section class="abs hero" role="img" aria-label="Group of friends posing inside a red-lit escape room"></section>
<div class="abs dots"><span></span><span class="on"></span><span></span></div>

<!-- rooms -->
<article class="abs room-card" style="left:113px">
  <div class="room-photo" role="img" aria-label="Freight elevator gate" style="background:linear-gradient(180deg,#6b4a3a,#2b2422)"></div>
  <h3>Elevator</h3><div class="diff">Difficulty: 10/10</div>
  <p>The main elevators are down so you'll need to take the freight elevator to the top floor if you want to get your award.</p>
  <span class="btn">Read More</span>
</article>
<article class="abs room-card" style="left:362px">
  <div class="room-photo" role="img" aria-label="Candy shop shelves" style="background:linear-gradient(180deg,#9bb0c8,#c9a28a)"></div>
  <h3>Candy Shop</h3><div class="diff">Difficulty: 7/10</div>
  <p>With all of the candy right before your eyes, find the golden ticket and win the prize!</p>
  <span class="btn">Read More</span>
</article>
<article class="abs room-card" style="left:609px">
  <div class="room-photo" role="img" aria-label="Bank vault door" style="background:linear-gradient(180deg,#2a2f36,#0f1114)"></div>
  <h3>Bank Heist</h3><div class="diff">Difficulty: 8/10</div>
  <p>With your family held hostage, the mob gave you one choice - rob the bank in exchange for their freedom.</p>
  <span class="btn">Read More</span>
</article>
<article class="abs room-card" style="left:858px">
  <div class="room-photo" role="img" aria-label="Players in orange jail outfits" style="background:linear-gradient(180deg,#3a3a3a,#c4502a)"></div>
  <h3>Jail Break</h3><div class="diff">Difficulty: 8/10</div>
  <p style="padding-top:16px">One Guard, One Goal:<br>get out.</p>
  <span class="btn">Read More</span>
</article>

<!-- corporate -->
<section class="abs corporate"></section>
<h2 class="section-title" style="top:1384px">Corporate Events</h2>
<div class="abs corp-frame"><div class="corp-photo" role="img" aria-label="Large corporate group posing in the lobby"></div></div>
<h2 class="abs center packages-title">Three Packages Offered</h2>

<div class="abs pkg-circle" style="left:160px">
  <svg width="100" height="100" viewBox="0 0 100 100" fill="none" stroke="#fff" stroke-width="5"><path d="M10 50 L50 12 L90 50"/><path d="M22 40 V90 H78 V40"/><path d="M42 90 V62 H58 V90"/><path d="M68 22 V34"/></svg>
</div>
<div class="abs pkg-circle" style="left:496px">
  <svg width="100" height="100" viewBox="0 0 100 100" fill="none" stroke="#fff" stroke-width="5"><path d="M18 10 H60 V40 H90 V74 H60 V92 H18 Z"/><path d="M60 40 V60"/><path d="M18 52 H34"/><path d="M40 10 V26"/></svg>
</div>
<div class="abs pkg-circle" style="left:834px">
  <svg width="104" height="104" viewBox="0 0 100 100" fill="none" stroke="#fff" stroke-width="4"><circle cx="50" cy="56" r="34"/><circle cx="50" cy="56" r="27" stroke-dasharray="2 6"/><path d="M42 14 H58 M50 14 V22 M20 26 L27 33 M80 26 L73 33 M50 56 L64 42"/></svg>
</div>

<div class="abs center pkg-name" style="left:98px">On-Site Multi-Room</div>
<div class="abs center pkg-name" style="left:434px">Off-Site Hot Seat Escape Room</div>
<div class="abs center pkg-name" style="left:772px">Off-Site Custom Escape Room Package</div>
<div class="abs center pkg-desc" style="left:98px">Come, enjoy, relax in our multi-room escape room facility with your team</div>
<div class="abs center pkg-desc" style="left:434px">Enjoy a 2 or 4 hour escape room in the new thrilling Hot Seat challenge!</div>
<div class="abs center pkg-desc" style="left:772px">Enjoy a customized escape room game to fit the theme you'd like to celebrate.</div>
<span class="btn" style="left:196px;top:2427px;width:134px;height:40px">Read More</span>
<span class="btn" style="left:532px;top:2427px;width:134px;height:40px">Read More</span>
<span class="btn" style="left:870px;top:2427px;width:134px;height:40px">Read More</span>

<div class="field" style="left:119px;top:2550px;width:314px;height:44px">Your Name</div>
<div class="field" style="left:443px;top:2550px;width:314px;height:44px">Your Phone</div>
<div class="field" style="left:765px;top:2550px;width:314px;height:44px">Your Email</div>
<div class="field" style="left:119px;top:2610px;width:960px;height:98px">Your Message</div>
<span class="btn" style="left:512px;top:2752px;width:176px;height:51px;border-radius:26px;font-size:13px">Send Message</span>

<!-- birthday -->
<h2 class="section-title" style="top:2935px">Birthday Parties</h2>
<p class="abs center intro">Celebrate this year in style by treating your family with an escape room birthday package. You and your loved ones have the choice of four escape rooms and will enjoy a private party afterwards in our party room. Either of these packages will be sure to satisfy your needs.</p>

<div class="abs price-card" style="left:140px">
  <div class="price-head">Birthday Parties</div>
  <div class="price-badge"><span>just</span><span>$150</span></div>
  <ul class="price-list">
    <li><svg width="16" height="12" viewBox="0 0 16 12" fill="none" stroke="#888" stroke-width="1.5"><path d="M1 6 L6 11 L15 1"/></svg>A private escape room event with party</li>
    <li><svg width="16" height="12" viewBox="0 0 16 12" fill="none" stroke="#888" stroke-width="1.5"><path d="M1 6 L6 11 L15 1"/></svg>room pizza and soda</li>
  </ul>
  <div class="price-rule"></div>
  <span class="ghost">Buy Now</span><span class="solid">Try It Free</span>
</div>
<div class="abs price-card" style="left:621px">
  <div class="price-head">Birthday Parties</div>
  <div class="price-badge"><span>just</span><span>$125</span></div>
  <ul class="price-list">
    <li><svg width="16" height="12" viewBox="0 0 16 12" fill="none" stroke="#888" stroke-width="1.5"><path d="M1 6 L6 11 L15 1"/></svg>A private escape room event with a party</li>
    <li><svg width="16" height="12" viewBox="0 0 16 12" fill="none" stroke="#888" stroke-width="1.5"><path d="M1 6 L6 11 L15 1"/></svg>room rental</li>
  </ul>
  <div class="price-rule"></div>
  <span class="ghost">Buy Now</span><span class="solid">Try It Free</span>
</div>
<p class="abs center note">Note: A $50 cleaning fee applies to all parties who don't clean after themselves</p>

<!-- booking band -->
<section class="abs contact-band"></section>
<div class="field" style="left:125px;top:3808px;width:197px;height:43px">Name</div>
<div class="field" style="left:332px;top:3808px;width:170px;height:43px">Number</div>
<div class="field" style="left:512px;top:3808px;width:160px;height:43px">Group Size</div>
<div class="field" style="left:682px;top:3808px;width:174px;height:43px">Which Package</div>
<div class="field" style="left:864px;top:3808px;width:209px;height:43px">Email</div>
<div class="field" style="left:125px;top:3867px;width:948px;height:99px">Description</div>
<div class="abs band-btn">Send Message</div>

<!-- faq -->
<p class="abs center faq-intro">An escape room is a themed environment where you and your friends must work together to complete the objectives through solving puzzles before time runs out. Most missions will lock you in while some of our missions do not.</p>
<div class="faq-item" style="left:121px;top:4322px"><svg width="24" height="24" viewBox="0 0 24 24" fill="none" stroke="#1c8fdc" stroke-width="1.5"><path d="M2 3 H22 V18 H10 L5 22 V18 H2 Z"/><path d="M9 8 a3 3 0 1 1 3 3 V13 M12 15.5 V16"/></svg>How do I make a reservation?</div>
<div class="faq-item" style="left:609px;top:4322px"><svg width="24" height="24" viewBox="0 0 24 24" fill="none" stroke="#1c8fdc" stroke-width="1.5"><path d="M2 3 H22 V18 H10 L5 22 V18 H2 Z"/><path d="M9 8 a3 3 0 1 1 3 3 V13 M12 15.5 V16"/></svg>How long does an escape last?</div>
<div class="faq-item" style="left:121px;top:4399px"><svg width="24" height="24" viewBox="0 0 24 24" fill="none" stroke="#1c8fdc" stroke-width="1.5"><path d="M2 3 H22 V18 H10 L5 22 V18 H2 Z"/><path d="M9 8 a3 3 0 1 1 3 3 V13 M12 15.5 V16"/></svg>I'm pregnant, can I participate?</div>
<div class="faq-item" style="left:609px;top:4399px"><svg width="24" height="24" viewBox="0 0 24 24" fill="none" stroke="#1c8fdc" stroke-width="1.5"><path d="M2 3 H22 V18 H10 L5 22 V18 H2 Z"/><path d="M9 8 a3 3 0 1 1 3 3 V13 M12 15.5 V16"/></svg>How can I redeem a voucher or promo code?</div>
<span class="btn" style="left:512px;top:4494px;width:176px;height:51px;border-radius:26px;font-size:13px">View More</span>

<!-- footer -->
<footer class="abs site-footer"></footer>
<h2 class="section-title" style="top:4690px;color:var(--white)">Contact Us</h2>
<div class="abs ct-circle" style="left:115px"><svg width="36" height="36" viewBox="0 0 24 24" fill="#fff"><path d="M6.6 10.8a15.1 15.1 0 0 0 6.6 6.6l2.2-2.2a1 1 0 0 1 1-.25 11.4 11.4 0 0 0 3.6.57 1 1 0 0 1 1 1V20a1 1 0 0 1-1 1A17 17 0 0 1 3 4a1 1 0 0 1 1-1h3.5a1 1 0 0 1 1 1c0 1.25.2 2.45.57 3.57a1 1 0 0 1-.25 1z"/></svg></div>
<div class="abs ct-circle" style="left:352px"><svg width="40" height="30" viewBox="0 0 40 30" fill="#fff"><path d="M2 2 H38 L20 16 Z"/><path d="M2 6 L20 20 L38 6 V28 H2 Z"/></svg></div>
<div class="abs ct-circle" style="left:637px"><svg width="30" height="40" viewBox="0 0 30 40" fill="none" stroke="#fff" stroke-width="3"><path d="M15 38 C15 38 3 22 3 14 a12 12 0 0 1 24 0 C27 22 15 38 15 38 Z"/><circle cx="15" cy="14" r="4.5"/></svg></div>
<div class="abs ct-circle" style="left:936px"><svg width="36" height="36" viewBox="0 0 36 36" fill="none" stroke="#fff" stroke-width="3"><circle cx="18" cy="18" r="14"/><path d="M18 9 V18 H25"/></svg></div>
<div class="abs ct-text" style="left:32px">(555) 014 2290</div>
<div class="abs ct-text" style="left:269px;width:260px">sales@puzzlevaultlarkfield.example</div>
<div class="abs ct-text" style="left:554px">1180 Meadowline Court, Suite 12,<br>Larkfield, VA 20999</div>
<div class="abs ct-text" style="left:843px;width:280px">Wednesday - Fridays (4 to 10pm)<br>Weekends (11am to 9pm).</div>
<div class="abs footer-rule"></div>
<p class="abs copyright">Copyrights © 2019 Puzzle Vault Larkfield. All rights reserved.</p>

</body>
</html>
```